Boutique custom software development company needs new business card

Our nearly 20 year old custom software development company would like to better include the fact that we are now providing Bitcoin services. These new services are B2B include education (how to acquire and securely hold Bitcoin) and integrating Bitcoin payments into existing ecommerce sites or other existing systems. Please keep the card clean and simple. Attached is our current design and some other files. vextorial.com

Target Market(s)

businesses owners interested in long term relationship

Industry/Entity Type

Custom software development and Bitcoin

Contact Information for Business Card

Dale Parker, dale@vextorial.com, vextorial.com, (888) 555-VXTRL

Font styles to use
Other font styles liked:
• monospace

Requirements
Must have
• double-sided
Nice to have
• clean and simple
Should not have
• physical address

```html
<!DOCTYPE html>
<html lang="en">
<head>
<meta charset="utf-8">
<title>Vextorial business card</title>
<link href="https://fonts.googleapis.com/css2?family=Montserrat:wght@400;500;700;800&display=swap" rel="stylesheet">
<style>
  :root {
    --stage: #3a3a3c;
    --card: #1b1c1e;
    --orange: #f07c1b;
    --blue: #3f73c0;
    --white: #f2f2f2;
    --rule: #5a5a5c;
    --pattern-a: #2a2a2c;
    --pattern-b: #3e3e41;
  }
  * { margin: 0; padding: 0; box-sizing: border-box; }
  html, body { width: 1200px; height: 689px; overflow: hidden; }
  body {
    background: var(--stage);
    font-family: "Montserrat", sans-serif;
    position: relative;
  }
  .card {
    position: absolute;
    top: 190px;
    width: 530px;
    height: 303px;
    border-radius: 22px;
    background: var(--card);
    overflow: hidden;
  }
  .card-back { left: 40px; }
  .card-front { left: 630px; }

  .back-pattern {
    position: absolute; inset: 0;
    background: linear-gradient(135deg, var(--pattern-a), var(--pattern-b) 55%, var(--pattern-a));
  }
  .back-mark {
    position: absolute;
    left: 0; right: 0; top: 132px;
    text-align: center;
    color: var(--orange);
    font-weight: 800;
    font-size: 30px;
    letter-spacing: 1px;
  }

  .stripes { position: absolute; inset: 0; }
  .brand {
    position: absolute;
    left: 0; right: 0; top: 34px;
    text-align: center;
  }
  .brand-name {
    color: var(--orange);
    font-weight: 800;
    font-size: 42px;
    letter-spacing: 1px;
    line-height: 1;
  }
  .brand-tagline {
    color: var(--blue);
    font-weight: 500;
    font-size: 14px;
    margin-top: 6px;
  }
  .person {
    position: absolute;
    left: 0; right: 0; top: 108px;
    display: flex; align-items: center; justify-content: center; gap: 12px;
  }
  .person-rule { width: 34px; height: 1px; background: var(--rule); }
  .person-name {
    color: var(--orange);
    font-weight: 700;
    font-size: 19px;
    letter-spacing: 1px;
    line-height: 24px;
  }
  .contact-icons {
    position: absolute;
    left: 0; right: 0; top: 142px;
    display: flex; justify-content: center; gap: 8px;
  }
  .contact-icon {
    width: 22px; height: 22px;
    border-radius: 5px;
    background: var(--blue);
    display: flex; align-items: center; justify-content: center;
  }
  .contact-list {
    position: absolute;
    left: 0; right: 0; top: 172px;
    text-align: center;
    color: var(--white);
    font-size: 13px;
    line-height: 18px;
  }
</style>
</head>
<body>
  <section class="card card-back">
    <div class="back-pattern" role="img" aria-label="Repeating tone-on-tone brand pattern"></div>
    <div class="back-mark">VEXTORIAL</div>
  </section>

  <section class="card card-front">
    <svg class="stripes" width="530" height="303" viewBox="0 0 530 303">
      <polygon points="0,284 530,244 530,249 0,289" fill="var(--orange)"/>
      <polygon points="0,293 530,253 530,273 0,313" fill="var(--blue)"/>
      <circle cx="470" cy="252" r="17" fill="var(--orange)" stroke="var(--card)" stroke-width="3"/>
    </svg>
    <div class="brand">
      <div class="brand-name">VEXTORIAL</div>
      <div class="brand-tagline">developer of custom applications</div>
    </div>
    <div class="person">
      <span class="person-rule"></span>
      <span class="person-name">DALE PARKER</span>
      <span class="person-rule"></span>
    </div>
    <div class="contact-icons">
      <span class="contact-icon">
        <svg width="13" height="13" viewBox="0 0 24 24"><path d="M6 3l3 0 2 5-2 1.5a11 11 0 0 0 5.5 5.5L16 13l5 2v3a2 2 0 0 1-2 2A16 16 0 0 1 4 5a2 2 0 0 1 2-2z" fill="none" stroke="#fff" stroke-width="2"/></svg>
      </span>
      <span class="contact-icon">
        <svg width="13" height="13" viewBox="0 0 24 24"><rect x="3" y="6" width="18" height="12" fill="none" stroke="#fff" stroke-width="2"/><path d="M3 6l9 7 9-7" fill="none" stroke="#fff" stroke-width="2"/></svg>
      </span>
      <span class="contact-icon">
        <svg width="13" height="13" viewBox="0 0 24 24"><circle cx="12" cy="12" r="9" fill="none" stroke="#fff" stroke-width="2"/><path d="M3 12h18M12 3c4 4 4 14 0 18M12 3c-4 4-4 14 0 18" fill="none" stroke="#fff" stroke-width="1.6"/></svg>
      </span>
    </div>
    <div class="contact-list">
      <div>(888) 555-VXTRL</div>
      <div>dale@vextorial.com</div>
      <div>vextorial.com</div>
    </div>
  </section>
</body>
</html>
```